Web Design Project for Communications Agency

The design I need (PSD file) is for an agency offering specialised PR and communications services for customers in the healthcare sector.

OBJECTIVES OF THE WEBSITE:
1. To promote the agency's communication services
2. To position Solène Brivard as an industry leader, an expert in healthcare PR and communications by highlighting blogposts and social media.

WHAT I NEED:
1st, I need the design for the Home Page ONLY.
Once approved, I will need the other pages designed as well. (Here is prototype that we've already developed for the Website that will guide you in the design:
http://qorvelle.net/solenebrivard/)

VISUAL INSPIRATION
We want to give this Website a "Flat Design" look. Here are some websites for inspiration :
- http://tavrolinkworks.com/#!/process
- http://www.brindlemoss.co/
- http://quellaroft.com/

Also, reuse images found on the company's current Website :
http://www.solenebrivard.com/fr/index.html

HOMEPAGE MAIN ELEMENTS:
1. Main menu : 6 sections
Accueil | Agence | Services | Approche | Publications | Contact

2. Main Call To Action (big dark rectangle in prototype):
Can be slider or just an information bloc.

3. Publications récentes :
The 4 latest blog posts must be features on the homepage (will be linked with the "Publications" section)

4. Dynamic Footer :
Contains a Chirpline feed and a Subscribe to our Newsletter feature (revecez nos publications)

OTHER PAGES (to design once Homepage is approved)
- Agence (about us)
- Services (our team)
- Approche (our approach)
- Publications (blog articles)
- Contact (Contact us)

Industry/Entity Type

Communications

Requirements
Must have
• Please refer to prototype :
http://qorvelle.net/solenebrivard/
Must have ALL features present in prototype.

Also, must reuse this picture in the design : http://solenebrivard.com/static/images/home-big-box.jpg

Finally, you will find attached the company logo.

```html
<!DOCTYPE html>
<html lang="fr">
<head>
<meta charset="utf-8">
<title>Solène Brivard — Gestion d'enjeux, affaires publiques</title>
<link rel="stylesheet" href="https://fonts.googleapis.com/css2?family=PT+Sans:wght@400;700&family=PT+Sans+Narrow:wght@700&display=swap">
<style>
  :root {
    --brand-red: #c1272d;
    --brand-red-dark: #a11d24;
    --nav-red: #c8323a;
    --ink: #2b2b2b;
    --muted: #6b6b6b;
    --hero-bg: #efedee;
    --page-bg: #ffffff;
    --footer-top: #333333;
    --footer-bottom: #161616;
    --footer-bar: #2a2a2a;
    --field-bg: #3d3d3d;
    --field-border: #4d4d4d;
    --rule: #dddddd;
  }
  * { box-sizing: border-box; margin: 0; padding: 0; }
  html, body { width: 686px; height: 1200px; overflow: hidden; }
  body {
    position: relative;
    background: var(--page-bg);
    font-family: "PT Sans", Arial, sans-serif;
    color: var(--ink);
  }

  /* Header */
  .site-header { position: absolute; left: 0; top: 0; width: 686px; height: 84px; }
  .brand {
    position: absolute; left: 53px; top: 13px;
    font-size: 24px; line-height: 22px; font-weight: 400;
    color: var(--brand-red); letter-spacing: -0.5px;
  }
  .lang-switch {
    position: absolute; right: 60px; top: 8px;
    font-size: 8px; color: var(--muted);
  }
  .lang-switch span { margin: 0 3px; }
  .social-links { position: absolute; right: 61px; top: 62px; display: flex; gap: 3px; }
  .social-links i { display: block; width: 12px; height: 12px; border-radius: 2px; }
  .social-links i:nth-child(1) { background: #3fa9e0; }
  .social-links i:nth-child(2) { background: #1f6fa8; }
  .social-links i:nth-child(3) { background: #e0a030; }

  /* Navigation */
  .main-nav {
    position: absolute; left: 0; top: 84px; width: 686px; height: 29px;
    background: linear-gradient(#d3434a, var(--brand-red-dark));
  }
  .tagline {
    position: absolute; left: 53px; top: 5px;
    font-family: "PT Sans Narrow", Arial, sans-serif; font-weight: 700;
    font-size: 7.5px; line-height: 8.5px; color: #fff; text-transform: uppercase;
  }
  .tagline .tagline-top { color: #6b1418; }
  .nav-list { position: absolute; left: 141px; top: 0; height: 29px; display: flex; list-style: none; }
  .nav-list li {
    height: 29px; line-height: 29px; padding: 0 16px;
    font-size: 11.5px; color: #fff; border-right: 1px solid rgba(255,255,255,0.35);
  }

  /* Hero */
  .hero { position: absolute; left: 0; top: 113px; width: 686px; height: 200px; background: var(--hero-bg); }
  .hero-title { position: absolute; left: 55px; top: 37px; font-size: 22px; font-weight: 400; color: #333; }
  .hero-subtitle { position: absolute; left: 55px; top: 64px; font-size: 13px; font-weight: 400; color: #333; }
  .hero-text { position: absolute; left: 55px; top: 86px; width: 360px; font-size: 7.5px; line-height: 12px; color: var(--muted); }
  .btn {
    display: inline-block; background: linear-gradient(#d23a41, var(--brand-red-dark));
    color: #fff; border: 1px solid #8f1a20;
  }
  .hero-cta { position: absolute; left: 56px; top: 118px; width: 93px; height: 22px; line-height: 20px; padding-left: 11px; font-size: 10px; }
  .hero-arrows { position: absolute; left: 54px; top: 170px; }
  .hero-visual {
    position: absolute; left: 434px; top: 17px; width: 192px; height: 183px;
    background: radial-gradient(circle at 50% 45%, #ffffff 0%, #e9e9e9 55%, #d9d9d9 100%);
  }
  .hero-visual::after {
    content: ""; position: absolute; left: 60px; top: 10px; width: 80px; height: 40px;
    background: linear-gradient(#c7333a, #a82128); opacity: 0.85;
  }

  /* Publications */
  .publications { position: absolute; left: 55px; top: 338px; width: 576px; }
  .section-title { font-family: "PT Sans Narrow", Arial, sans-serif; font-weight: 700; font-size: 17px; color: #333; }
  .post { position: absolute; left: 0; width: 576px; height: 100px; }
  .post-media { position: absolute; left: 0; top: 0; width: 218px; height: 99px; border: 1px solid var(--rule); }
  .post-body { position: absolute; left: 232px; top: 0; width: 344px; }
  .post-title { font-size: 12px; font-weight: 400; color: #222; line-height: 14px; }
  .post-date { font-size: 7px; color: var(--brand-red); margin-top: 2px; }
  .post-excerpt { font-size: 7px; line-height: 11.3px; color: var(--muted); margin-top: 4px; }
  .post-more { margin-top: 5px; font-size: 7px; color: var(--muted); }
  .post-link { margin-top: 6px; width: 74px; height: 18px; line-height: 16px; text-align: center; font-size: 7px; }

  /* Footer */
  .site-footer {
    position: absolute; left: 0; top: 949px; width: 686px; height: 219px;
    background: linear-gradient(var(--footer-top), var(--footer-bottom));
  }
  .feed { position: absolute; left: 55px; top: 26px; width: 230px; }
  .feed-brand { font-size: 32px; font-weight: 700; color: #35a8e0; line-height: 36px; }
  .tweet { margin-top: 10px; font-size: 7px; line-height: 11px; color: #e6e6e6; }
  .tweet:first-of-type { margin-top: 8px; }
  .tweet em { font-style: normal; color: #e0434b; }
  .footer-divider { position: absolute; left: 317px; top: 32px; width: 1px; height: 146px; background: #444; }
  .newsletter { position: absolute; left: 347px; top: 30px; width: 222px; }
  .newsletter h2 { font-size: 17px; font-weight: 400; color: #fff; }
  .field {
    display: block; width: 221px; height: 24px; margin-top: 8px;
    background: var(--field-bg); border: 1px solid var(--field-border); border-radius: 2px;
    padding-left: 9px; line-height: 22px; font-size: 8px; color: #9a9a9a;
  }
  .field:first-of-type { margin-top: 10px; }
  .subscribe { position: absolute; right: 1px; top: 107px; width: 89px; height: 22px; line-height: 20px; text-align: center; font-size: 10px; }
  .legal-bar {
    position: absolute; left: 0; top: 1168px; width: 686px; height: 32px;
    background: var(--footer-bar); border-top: 1px solid #3a3a3a;
    font-size: 7px; color: #8a8a8a; padding: 12px 0 0 63px;
  }
</style>
</head>
<body>
  <header class="site-header">
    <div class="brand">solène<br>brivard</div>
    <div class="lang-switch">English<span>|</span>French</div>
    <div class="social-links" aria-label="Réseaux sociaux"><i></i><i></i><i></i></div>
  </header>

  <nav class="main-nav">
    <div class="tagline"><span class="tagline-top">Gestion d'enjeux</span><br>Affaires publiques</div>
    <ul class="nav-list">
      <li>Accueil</li><li>Agence</li><li>Services</li><li>Approche</li><li>Publications</li><li>Contact</li>
    </ul>
  </nav>

  <section class="hero">
    <h1 class="hero-title">Cabinet-conseil en Communications</h1>
    <h2 class="hero-subtitle">et affaires publiques spécialisé dans le secteur de la santé.</h2>
    <p class="hero-text">Phasellus felis dolor, scelerisque a, tempus eget, lobortis id, libero. Donec scelerisque leo ac risus. Praesent sit amet est. In dictum dolor  Eu dictum porttitor enim felis viverra</p>
    <span class="btn hero-cta">En savoir plus ›</span>
    <svg class="hero-arrows" width="20" height="12" viewBox="0 0 20 12" aria-label="Précédent / suivant">
      <path d="M6 1 L1 6 L6 11" fill="none" stroke="#333" stroke-width="1.4"/>
      <path d="M13 1 L18 6 L13 11" fill="none" stroke="#333" stroke-width="1.4"/>
    </svg>
    <div class="hero-visual" role="img" aria-label="Cube blanc aux carrés rouges formant une croix"></div>
  </section>

  <section class="publications">
    <h2 class="section-title">Publication récentes</h2>

    <article class="post" style="top:28px">
      <div class="post-media" role="img" aria-label="Photo d'une professionnelle souriante au bureau" style="background:linear-gradient(90deg,#b9c6d2,#e9e3de 60%,#3a3d48)"></div>
      <div class="post-body">
        <h3 class="post-title">Nunc tempus felis vitae urna</h3>
        <p class="post-date">23 July 2013</p>
        <p class="post-excerpt">Duis tincidunt lectus quis dui viverra vestibulum. Suspendisse vulputate aliquam dui. Nulla elementum dui ut augue. Aliquam vehicula mi at mauris. Maecenas placerat, nisl at consequat rhoncus, sem nunc gravida justo, quis eleifend arcu velit quis lacus. Morbi magna magna, tincidunt a, mattis non, imperdiet vitae, tellus. Sed odio est, auctor ac, sollicitudin in, consequat vitae, orci. Fusce id felis.</p>
        <p class="post-more">Nunc tempus felis vitae urna. Vivamus porttitor, g, purus nisi eleifend libero, a tempus libero lectus</p>
        <span class="btn post-link">Article Complete</span>
      </div>
    </article>

    <article class="post" style="top:173px">
      <div class="post-media" role="img" aria-label="Photo d'une équipe réunie autour d'un ordinateur" style="background:linear-gradient(90deg,#d8cfc6,#a9b3c2 50%,#e0a0b0)"></div>
      <div class="post-body">
        <h3 class="post-title">Ut nisi erat fermentum vel</h3>
        <p class="post-date">23 July 2013</p>
        <p class="post-excerpt">Duis tincidunt lectus quis dui viverra vestibulum. Suspendisse vulputate aliquam dui. Nulla elementum dui ut augue. Aliquam vehicula mi at mauris. Maecenas placerat, nisl at consequat rhoncus, sem nunc gravida justo, quis eleifend arcu velit quis lacus. Morbi magna magna, tincidunt a, mattis non, imperdiet vitae, tellus. Sed odio est, auctor ac, sollicitudin in, consequat vitae, orci. Fusce id felis.</p>
        <p class="post-more">Nunc tempus felis vitae urna. Vivamus porttitor, g, purus nisi eleifend libero, a tempus libero lectus</p>
        <span class="btn post-link">Article Complete</span>
      </div>
    </article>

    <article class="post" style="top:317px">
      <div class="post-media" role="img" aria-label="Photo d'un conférencier devant un auditoire" style="background:linear-gradient(180deg,#dfe5ec,#b7c2ce 55%,#3b3633)"></div>
      <div class="post-body">
        <h3 class="post-title">Morbi magna magna tincidunt</h3>
        <p class="post-date">23 July 2013</p>
        <p class="post-excerpt">Duis tincidunt lectus quis dui viverra vestibulum. Suspendisse vulputate aliquam dui. Nulla elementum dui ut augue. Aliquam vehicula mi at mauris. Maecenas placerat, nisl at consequat rhoncus, sem nunc gravida justo, quis eleifend arcu velit quis lacus. Morbi magna magna, tincidunt a, mattis non, imperdiet vitae, tellus. Sed odio est, auctor ac, sollicitudin in, consequat vitae, orci. Fusce id felis.</p>
        <p class="post-more">Nunc tempus felis vitae urna. Vivamus porttitor, g, purus nisi eleifend libero, a tempus libero lectus</p>
        <span class="btn post-link">Article Complete</span>
      </div>
    </article>

    <article class="post" style="top:462px">
      <div class="post-media" role="img" aria-label="Photo d'une réunion d'affaires autour d'une table" style="background:linear-gradient(90deg,#c9c2bb,#6e5a4c 40%,#e6e8ea 75%,#8c8f94)"></div>
      <div class="post-body">
        <h3 class="post-title">Duis sed tellus et tortor vestibulum gravida</h3>
        <p class="post-date">23 July 2013</p>
        <p class="post-excerpt">Duis tincidunt lectus quis dui viverra vestibulum. Suspendisse vulputate aliquam dui. Nulla elementum dui ut augue. Aliquam vehicula mi at mauris. Maecenas placerat, nisl at consequat rhoncus, sem nunc gravida justo, quis eleifend arcu velit quis lacus. Morbi magna magna, tincidunt a, mattis non, imperdiet vitae, tellus. Sed odio est, auctor ac, sollicitudin in, consequat vitae, orci. Fusce id felis.</p>
        <p class="post-more">Nunc tempus felis vitae urna. Vivamus porttitor, g, purus nisi eleifend libero, a tempus libero lectus</p>
        <span class="btn post-link">Article Complete</span>
      </div>
    </article>
  </section>

  <footer class="site-footer">
    <div class="feed">
      <div class="feed-brand">chirpline</div>
      <p class="tweet">Velit esse cillum dolore eu fugiat nulla pariatur. Excepteur sint occaecat cupidatat non proident. <em>@SoleneBrivard #EnjeuSanté</em></p>
      <p class="tweet">Velit esse cillum dolore eu fugiat nulla pariatur. Excepteur sint occaecat cupidatat non proident. <em>@SoleneBrivard #EnjeuSanté</em></p>
      <p class="tweet">Phasellus felis dolor, scelerisque a, tempus eget, lobortis id, libero. Donec scelerisque leo ac risus. Praesent sit amet est. In dictum, dolor eu dictum porttitor, enim felis viverra <em>@SoleneBrivard #EnjeuSanté</em></p>
    </div>
    <div class="footer-divider"></div>
    <div class="newsletter">
      <h2>Recevez nos publications</h2>
      <span class="field">Votre nom</span>
      <span class="field">Votre courriel</span>
      <span class="btn subscribe">Abonnez-vous</span>
    </div>
  </footer>

  <div class="legal-bar">© 2013 Company Name.  All right reserved.  Term of Use</div>
</body>
</html>
```